Modern looking signage for dental office.

Exterior signage for passing cars
Updates
Need extra days to review
Target Market(s)
Cars passing by
Font styles to use
Sans Serif
Colors
3276b5
Requirements
Must have
- Logo
- OPEN ON SUTURDAY AND SUNDAY
- NIGHT CLINIC AVAILABLE
- PLEASE USE THE FONT TYPE IN FILE 4 UPLOADED BELOW.
- (847) 302-7469
- Modern looking

```html
<!DOCTYPE html>
<html lang="en">
<head>
<meta charset="UTF-8">
<title>Summit Dental – Exterior Sign</title>
<link href="https://fonts.googleapis.com/css2?family=Montserrat:wght@400&family=Roboto+Condensed:wght@800&display=swap" rel="stylesheet">
<style>
  :root {
    --brand-blue: #0d5699;
    --ink: #3a3838;
    --white: #ffffff;
    --panel-light: #f4f4f4;
    --panel-shade: #dadada;
    --page: #e6e8eb;
  }
  html, body {
    margin: 0;
    width: 1200px;
    height: 1200px;
    overflow: hidden;
    background: var(--page);
  }
  .canvas {
    position: relative;
    width: 1200px;
    height: 1200px;
  }
  .sign {
    position: absolute;
    left: 40px;
    top: 280px;
    width: 1120px;
    height: 640px;
    background: var(--white);
    overflow: hidden;
    box-shadow: 0 6px 24px rgba(0,0,0,0.12);
  }
  .sign-shapes {
    position: absolute;
    inset: 0;
  }
  .brand {
    position: absolute;
    left: 205px;
    top: 48px;
    display: flex;
    align-items: center;
    gap: 28px;
  }
  .brand-mark {
    width: 136px;
    height: 136px;
    border-radius: 50%;
    border: 3px solid var(--ink);
    background: var(--white);
    box-sizing: border-box;
  }
  .brand-name {
    font-family: "Montserrat", sans-serif;
    font-weight: 400;
    font-size: 74px;
    letter-spacing: 2px;
    color: var(--ink);
    line-height: 1;
    white-space: nowrap;
  }
  .tagline {
    position: absolute;
    left: 370px;
    top: 192px;
    width: 720px;
    text-align: center;
    font-family: "Montserrat", sans-serif;
    font-weight: 400;
    font-size: 34px;
    color: var(--ink);
    letter-spacing: 0.5px;
    white-space: nowrap;
  }
  .headline {
    font-family: "Roboto Condensed", sans-serif;
    font-weight: 800;
    line-height: 1;
    margin: 0;
    white-space: nowrap;
  }
  .night-clinic {
    position: absolute;
    left: 42px;
    top: 240px;
    font-size: 84px;
    line-height: 1.22;
    color: var(--brand-blue);
  }
  .weekend {
    position: absolute;
    right: 32px;
    top: 312px;
    text-align: right;
    font-size: 66px;
    line-height: 1.12;
    color: var(--white);
  }
  .phone {
    position: absolute;
    right: 32px;
    top: 520px;
    font-size: 92px;
    color: var(--white);
    letter-spacing: 1px;
  }
</style>
</head>
<body>
<main class="canvas">
  <section class="sign" aria-label="Summit Dental exterior sign">
    <svg class="sign-shapes" width="1120" height="640" viewBox="0 0 1120 640" aria-hidden="true">
      <defs>
        <radialGradient id="panelGlow" cx="0.45" cy="0.55" r="0.75">
          <stop offset="0" stop-color="#ffffff"/>
          <stop offset="0.55" stop-color="#eeeeee"/>
          <stop offset="1" stop-color="#d6d6d6"/>
        </radialGradient>
      </defs>
      <polygon class="side-panel" points="0,0 215,0 500,640 0,640" fill="url(#panelGlow)"/>
      <polygon class="band-weekend" points="343,288 1120,288 1120,474 426,474" fill="var(--brand-blue)"/>
      <polygon class="band-phone" points="438,500 1120,500 1120,640 500,640" fill="var(--brand-blue)"/>
    </svg>

    <div class="brand">
      <span class="brand-mark" aria-hidden="true"></span>
      <span class="brand-name">SUMMIT DENTAL</span>
    </div>
    <p class="tagline" style="margin:0">MODERN GENERAL DENTISTRY</p>

    <h2 class="headline night-clinic">Night<br>Clinic<br>Available</h2>
    <h2 class="headline weekend">Open on<br>Saturday and Sunday</h2>
    <p class="headline phone">(847) 302-7469</p>
  </section>
</main>
</body>
</html>
```